Veltrano.co - Polar Expeditions Specialists

We need a modern, visually striking business card for Veltrano.co, a company specialized in selling expedition cruises to the most remote regions on Earth, with a focus on the Arctic and Antarctica. The design should instantly communicate that the cardholder is an expert in polar travel. Use clean, premium aesthetics with cool tones like icy blue and white, possibly incorporating polar imagery (ice, glaciers, penguins, etc.)

Attached the logo

Contact Information for Business Card

Feels high-end and trustworthy.. Visually memorable — encourages people to keep it

Colors
0054AA
0677BA
7BADD7
CADEEF
E8F1F8

Requirements
Must have
• ice, glaciers, penguins, montains
Nice to have
• modern, transparente,

```html
<!DOCTYPE html>
<html lang="en">
<head>
<meta charset="UTF-8">
<title>Veltrano.co – Business Card</title>
<link href="https://fonts.googleapis.com/css2?family=Poppins:wght@600;700&family=Lato:wght@400;700&display=swap" rel="stylesheet">
<style>
  :root {
    --brand-blue: #3476b5;
    --card-white: #ffffff;
    --ink: #1a1a1a;
    --backdrop: #2b2b2b;
  }
  * { margin: 0; padding: 0; box-sizing: border-box; }
  html, body { width: 1200px; height: 1200px; overflow: hidden; }
  body { background: var(--backdrop); position: relative; font-family: "Lato", sans-serif; }

  .card { position: absolute; border-radius: 28px; box-shadow: 0 6px 18px rgba(0,0,0,.45); }
  .card--front { left: 176px; top: 101px; width: 864px; height: 492px; background: var(--brand-blue); }
  .card--back  { left: 179px; top: 621px; width: 850px; height: 482px; background: var(--card-white); }

  .brand { position: absolute; text-align: center; font-family: "Poppins", sans-serif; }
  .brand__mark { border-radius: 50%; margin: 0 auto; }
  .brand__name { font-weight: 700; line-height: 1; letter-spacing: -0.5px; }
  .brand__tagline { font-weight: 600; line-height: 1; }

  .card--front .brand { left: 0; width: 100%; top: 112px; color: var(--card-white); }
  .card--front .brand__mark { width: 120px; height: 120px; background: var(--card-white); }
  .card--front .brand__name { font-size: 76px; margin-top: 44px; }
  .card--front .brand__tagline { font-size: 22px; margin-top: 12px; }

  .card--back .brand { left: 60px; width: 365px; top: 150px; color: var(--brand-blue); }
  .card--back .brand__mark { width: 98px; height: 98px; background: var(--brand-blue); }
  .card--back .brand__name { font-size: 52px; margin-top: 30px; }
  .card--back .brand__tagline { font-size: 17px; margin-top: 8px; }

  .divider { position: absolute; left: 430px; top: 103px; width: 2px; height: 285px; background: var(--brand-blue); }

  .contact { position: absolute; left: 471px; top: 101px; color: var(--ink); }
  .contact__name { font-weight: 700; font-size: 31px; color: var(--brand-blue); line-height: 1.2; }
  .contact__role { font-size: 21px; margin-top: 4px; }
  .contact__list { list-style: none; margin-top: 24px; }
  .contact__item { display: flex; align-items: center; font-size: 22px; height: 32px; }
  .contact__icon { width: 24px; height: 24px; margin-right: 19px; fill: var(--brand-blue); flex: none; }
  .contact__address { font-size: 22px; line-height: 32px; margin-top: 20px; }
</style>
</head>
<body>
  <section class="card card--front">
    <div class="brand">
      <div class="brand__mark"></div>
      <div class="brand__name">Veltrano.co</div>
      <div class="brand__tagline">Polar Expeditions Specialists</div>
    </div>
  </section>

  <section class="card card--back">
    <div class="brand">
      <div class="brand__mark"></div>
      <div class="brand__name">Veltrano.co</div>
      <div class="brand__tagline">Polar Expeditions Specialists</div>
    </div>

    <div class="divider"></div>

    <div class="contact">
      <div class="contact__name">Marcus Ellery</div>
      <div class="contact__role">Owner</div>
      <ul class="contact__list">
        <li class="contact__item">
          <svg class="contact__icon" viewBox="0 0 24 24"><path d="M6.6 10.8a15 15 0 0 0 6.6 6.6l2.2-2.2a1 1 0 0 1 1-.25 11.4 11.4 0 0 0 3.6.57 1 1 0 0 1 1 1V20a1 1 0 0 1-1 1A17 17 0 0 1 3 4a1 1 0 0 1 1-1h3.5a1 1 0 0 1 1 1c0 1.25.2 2.45.57 3.57a1 1 0 0 1-.25 1z"/></svg>
          044-987 654 321
        </li>
        <li class="contact__item">
          <svg class="contact__icon" viewBox="0 0 24 24"><path d="M2 5h20v14H2z" fill="none"/><path d="M2 5h20v2l-10 6L2 7zM2 9l10 6 10-6v10H2z"/></svg>
          hello@veltrano.co
        </li>
        <li class="contact__item">
          <svg class="contact__icon" viewBox="0 0 24 24"><circle cx="12" cy="12" r="10" fill="none" stroke="#3476b5" stroke-width="2"/><path d="M12 2a10 10 0 0 0 0 20V2zM2 12h20" fill="none" stroke="#3476b5" stroke-width="2"/></svg>
          www.veltrano.co
        </li>
      </ul>
      <p class="contact__address">421, Address line goes here<br>45452, Country name</p>
    </div>
  </section>
</body>
</html>
```